Business card for law firm

Need business card for new law firm. Think confident, authoritative, conservative, but not stuffy or old-fashioned.

Contact Information for Business Card

Content for card - logo (uploaded), plus the following:

Paul Whitcombe (larger font)
Managing Partner (larger font, but not as large as name)
Level 9, 7 Ferris Lane
Sydney NSW 2000
Main Tel 02 9364 2710
Direct Tel 02 8472 3159
Email paul@qvlegal.com.au
www.qvlegal.com.au

Letterhead design should include logo plus:
Level 9, 7 Ferris Lane
Sydney NSW 2000
Tel 02 8472 3159
www.qvlegal.com.au

```html
<!DOCTYPE html>
<html lang="en">
<head>
<meta charset="utf-8">
<title>Quayvale Legal – Business Card</title>
<link href="https://fonts.googleapis.com/css2?family=Lora:wght@400&family=Roboto:wght@400&display=swap" rel="stylesheet">
<style>
  :root {
    --page: #e4e4e4;
    --paper: #ffffff;
    --navy: #0b1f56;
    --navy-soft: #1e356d;
    --ink: #0a0a0a;
    --grey: #555a63;
    --rule: #c9c9c9;
  }
  * { margin: 0; padding: 0; box-sizing: border-box; }
  html, body {
    width: 1125px; height: 1200px; overflow: hidden;
    background: var(--page);
  }
  .card {
    position: absolute; left: 171px; width: 826px; height: 472px;
    box-shadow: 0 2px 4px rgba(0,0,0,.25);
    overflow: hidden;
  }
  .card--front { top: 106px; background: var(--paper); }
  .card--back { top: 639px; background: var(--navy); }

  .brand { position: absolute; left: 60px; width: 370px; top: 140px; text-align: center; }
  .brand__mark { width: 60px; height: 60px; background: var(--navy); margin: 0 auto 52px; }
  .brand__name {
    font-family: "Lora", serif; font-weight: 400; color: var(--ink);
    font-size: 46px; line-height: 1; letter-spacing: 1px;
  }
  .brand__sub {
    font-family: "Lora", serif; font-weight: 400; color: var(--ink);
    font-size: 17px; letter-spacing: 19px; margin-top: 14px; padding-left: 19px;
  }

  .divider { position: absolute; left: 438px; top: 100px; width: 1px; height: 250px; background: var(--rule); }

  .contact { position: absolute; left: 476px; top: 112px; font-family: "Lora", serif; }
  .contact__name { color: var(--navy); font-size: 33px; line-height: 1; letter-spacing: .3px; }
  .contact__title { color: var(--ink); font-size: 20px; line-height: 1; margin-top: 4px; }
  .contact__address { color: var(--grey); font-size: 19px; line-height: 25px; margin-top: 22px; }
  .contact__list { list-style: none; margin-top: 13px; }
  .contact__item { display: flex; align-items: center; color: var(--grey); font-size: 19px; line-height: 26.5px; }
  .contact__icon { width: 18px; height: 18px; margin-right: 12px; fill: var(--navy); }

  .bands { position: absolute; left: 0; bottom: 0; }
  .web--front {
    position: absolute; left: 535px; top: 431px;
    font-family: "Lora", serif; color: #fff; font-size: 19px; letter-spacing: 4.6px;
  }

  .pattern {
    position: absolute; inset: 0;
    background: linear-gradient(135deg, var(--navy-soft) 0%, var(--navy) 50%, var(--navy-soft) 100%);
  }
  .back-brand { position: absolute; left: 0; right: 0; top: 150px; text-align: center; }
  .back-brand .brand__mark { background: #fff; margin-bottom: 30px; }
  .back-brand .brand__name, .back-brand .brand__sub { color: #fff; }
  .web--back {
    position: absolute; left: 0; right: 0; top: 405px; text-align: center;
    font-family: "Roboto", sans-serif; color: #fff; font-size: 19px; letter-spacing: 8px;
  }
</style>
</head>
<body>
  <section class="card card--front">
    <div class="brand">
      <div class="brand__mark"></div>
      <div class="brand__name">QUAYVALE</div>
      <div class="brand__sub">LEGAL</div>
    </div>

    <div class="divider"></div>

    <div class="contact">
      <div class="contact__name">PAUL WHITCOMBE</div>
      <div class="contact__title">MANAGING PARTNER</div>
      <div class="contact__address">Level 9, 7 Ferris Lane<br>Sydney NSW 2000</div>
      <ul class="contact__list">
        <li class="contact__item">
          <svg class="contact__icon" viewBox="0 0 24 24"><path d="M6.6 10.8a15.1 15.1 0 0 0 6.6 6.6l2.2-2.2a1 1 0 0 1 1-.25 11.4 11.4 0 0 0 3.6.57 1 1 0 0 1 1 1V20a1 1 0 0 1-1 1A17 17 0 0 1 3 4a1 1 0 0 1 1-1h3.5a1 1 0 0 1 1 1c0 1.25.2 2.45.57 3.57a1 1 0 0 1-.25 1z"/></svg>
          02 9364 2710
        </li>
        <li class="contact__item">
          <svg class="contact__icon" viewBox="0 0 24 24"><path d="M6.6 10.8a15.1 15.1 0 0 0 6.6 6.6l2.2-2.2a1 1 0 0 1 1-.25 11.4 11.4 0 0 0 3.6.57 1 1 0 0 1 1 1V20a1 1 0 0 1-1 1A17 17 0 0 1 3 4a1 1 0 0 1 1-1h3.5a1 1 0 0 1 1 1c0 1.25.2 2.45.57 3.57a1 1 0 0 1-.25 1z"/></svg>
          02 8472 3159
        </li>
        <li class="contact__item">
          <svg class="contact__icon" viewBox="0 0 24 24"><path d="M2 5h20v14H2z M3.5 6.5 12 13l8.5-6.5" fill="none" stroke="var(--navy)" stroke-width="0"/><path d="M2 5h20v14H2zm2 2v.3l8 5.6 8-5.6V7zm0 2.7V17h16V9.7l-8 5.6z"/></svg>
          paul@qvlegal.com.au
        </li>
      </ul>
    </div>

    <svg class="bands" width="826" height="60" viewBox="0 0 826 60">
      <polygon points="0,37 455,37 437,60 0,60" fill="var(--ink)"/>
      <polygon points="489,8 826,8 826,60 441,60" fill="var(--navy)"/>
    </svg>
    <div class="web--front">www.qvlegal.com.au</div>
  </section>

  <section class="card card--back">
    <div class="pattern" role="img" aria-label="Repeating brand pattern in navy tones"></div>
    <div class="back-brand">
      <div class="brand__mark"></div>
      <div class="brand__name">QUAYVALE</div>
      <div class="brand__sub">LEGAL</div>
    </div>
    <div class="web--back">www.qvlegal.com.au</div>
  </section>
</body>
</html>
```